Coffeeshop menu for filter tip

We want to have a cannabis (coffeeshop) menu in the size 25mm wide x 60mm wide. Some examples attached.

it must have the following text:
Menu

WEED p/g
Oblivane €16
Cloudplum €14
Tide Runner €14
Quincefig €16
Mega Marsh €14
Grey Heron €14

HASH p/g
Tashar Amber €12
Pebble Frost€11
Lime Dunes €14
Ash Petal €10

Target Market(s)

tourist in Amsterdam

Requirements
Nice to have
• cannabis sign leaf
• No Cigarettes allowed symbol

```html
<!DOCTYPE html>
<html lang="en">
<head>
<meta charset="utf-8">
<title>Amsterdam Menu – Filter Tip Card</title>
<link rel="stylesheet" href="https://fonts.googleapis.com/css2?family=Fenix&family=Merriweather:wght@700;900&family=Roboto+Condensed:wght@700&display=swap">
<style>
  :root {
    --page-bg: #fdfdfd;
    --card-bg: #ccffcc;
    --deep-green: #0b6410;
    --mid-green: #2f8f2a;
    --leaf-green: #3fa535;
    --ink: #0f3d12;
    --rule: #1d4a1d;
    --white: #ffffff;
    --stop-red: #e3141b;
  }
  * { margin: 0; padding: 0; box-sizing: border-box; }
  html, body { width: 1200px; height: 780px; overflow: hidden; background: var(--page-bg); }

  .menu-card {
    position: absolute; left: 466px; top: 32px;
    width: 273px; height: 654px;
    background: var(--card-bg);
    overflow: hidden;
  }
  .card-shape { position: absolute; left: 0; width: 273px; display: block; }
  .header-shape { top: 0; height: 130px; }
  .footer-shape { bottom: 0; height: 80px; }

  .ornament-band {
    position: absolute; left: 0; top: 2px; width: 273px; height: 76px;
    background: linear-gradient(180deg, #2a9a2a 0%, #1b7a1c 40%, var(--deep-green) 100%);
    opacity: .85;
  }
  .leaf-badge {
    position: absolute; left: 112px; top: 10px; width: 48px; height: 48px;
    border-radius: 50%; background: var(--white);
    border: 2px solid var(--deep-green);
    display: flex; align-items: center; justify-content: center;
  }
  .leaf-badge span {
    width: 32px; height: 28px; border-radius: 50%;
    background: radial-gradient(circle, var(--leaf-green), var(--deep-green));
  }
  .city-name {
    position: absolute; left: 0; width: 273px; top: 60px; text-align: center;
    font-family: "Merriweather", serif; font-weight: 900; font-size: 11px;
    letter-spacing: .5px; color: var(--white);
  }
  .menu-title {
    position: absolute; left: 0; width: 273px; top: 74px; text-align: center;
    font-family: "Merriweather", serif; font-weight: 900; font-size: 21px;
    letter-spacing: 1px; color: var(--white);
  }

  .section-tab {
    position: absolute; height: 31px;
    display: flex; align-items: center;
    background: var(--deep-green); color: var(--white);
    font-family: "Merriweather", serif; font-weight: 900;
    font-size: 25px; line-height: 1;
  }
  .section-tab .tab-label { display: block; line-height: 1; padding-top: 3px; }
  .section-tab .tab-unit {
    align-self: flex-start; margin: 3px 0 0 8px;
    font-size: 12px; font-weight: 700; line-height: 1;
  }
  .tab-weed { left: 0; top: 161px; width: 182px; padding-left: 8px; border-radius: 0 16px 16px 0; }
  .tab-hash { left: 118px; top: 404px; width: 155px; padding-left: 34px; border-radius: 16px 0 0 16px; }

  .price-list { position: absolute; list-style: none; }
  .weed-list { left: 6px; top: 193px; width: 254px; }
  .hash-list { left: 10px; top: 441px; width: 250px; }
  .price-row {
    display: flex; justify-content: space-between; align-items: baseline;
    height: 31px; padding: 2px 4px 0 7px;
    border-bottom: 2px solid var(--rule);
    font-family: "Fenix", serif; color: var(--ink);
  }
  .hash-list .price-row { height: 33px; padding-left: 8px; }
  .hash-list .price-row:last-child { border-bottom: none; }
  .weed-list .price-row:last-child { height: 40px; }
  .item-name { font-size: 22px; }
  .item-price { font-size: 25px; font-weight: 700; }
  .item-price .currency { font-size: 18px; font-weight: 400; margin-right: 6px; }

  .footer-note {
    position: absolute; left: 100px; bottom: 14px;
    font-family: "Roboto Condensed", sans-serif; font-weight: 700;
    font-size: 16px; color: var(--white);
  }
  .no-smoking { position: absolute; left: 218px; top: 606px; width: 46px; height: 46px; }
</style>
</head>
<body>
  <main class="menu-card">
    <svg class="card-shape header-shape" viewBox="0 0 273 130" aria-hidden="true">
      <path d="M0 0 H273 V102 C240 100 228 112 215 130 C190 112 150 100 80 106 C40 110 15 114 0 116 Z" fill="var(--deep-green)"/>
    </svg>
    <div class="ornament-band" role="img" aria-label="Green cannabis leaf texture with lattice and scroll ornament border"></div>
    <div class="leaf-badge" role="img" aria-label="Cannabis leaf emblem"><span></span></div>
    <p class="city-name">AMSTERDAM</p>
    <h1 class="menu-title">MENU</h1>

    <h2 class="section-tab tab-weed"><span class="tab-label">WEED</span><span class="tab-unit">p/g</span></h2>
    <ul class="price-list weed-list">
      <li class="price-row"><span class="item-name">Oblivane</span><span class="item-price"><span class="currency">€</span>16</span></li>
      <li class="price-row"><span class="item-name">Cloudplum</span><span class="item-price"><span class="currency">€</span>16</span></li>
      <li class="price-row"><span class="item-name">Tide Runner</span><span class="item-price"><span class="currency">€</span>14</span></li>
      <li class="price-row"><span class="item-name">Quincefig</span><span class="item-price"><span class="currency">€</span>16</span></li>
      <li class="price-row"><span class="item-name">Mega Marsh</span><span class="item-price"><span class="currency">€</span>14</span></li>
      <li class="price-row"><span class="item-name">Grey Heron</span><span class="item-price"><span class="currency">€</span>14</span></li>
    </ul>

    <h2 class="section-tab tab-hash"><span class="tab-label">HASH</span><span class="tab-unit">p/g</span></h2>
    <ul class="price-list hash-list">
      <li class="price-row"><span class="item-name">Tashar Amber</span><span class="item-price"><span class="currency">€</span>12</span></li>
      <li class="price-row"><span class="item-name">Pebble Frost</span><span class="item-price"><span class="currency">€</span>11</span></li>
      <li class="price-row"><span class="item-name">Lime Dunes</span><span class="item-price"><span class="currency">€</span>14</span></li>
      <li class="price-row"><span class="item-name">Ash Petal</span><span class="item-price"><span class="currency">€</span>10</span></li>
    </ul>

    <svg class="card-shape footer-shape" viewBox="0 0 273 80" aria-hidden="true">
      <path d="M0 40 C60 44 150 44 200 34 C240 26 262 14 273 0 V80 H0 Z" fill="var(--deep-green)"/>
    </svg>
    <p class="footer-note">NO SIGARETS</p>
    <svg class="no-smoking" viewBox="0 0 46 46" role="img" aria-label="No smoking">
      <circle cx="23" cy="23" r="20" fill="var(--white)"/>
      <rect x="8" y="20" width="26" height="6" fill="#222"/>
      <rect x="34" y="20" width="4" height="6" fill="#f08a24"/>
      <circle cx="23" cy="23" r="18" fill="none" stroke="var(--stop-red)" stroke-width="4"/>
      <line x1="10" y1="10" x2="36" y2="36" stroke="var(--stop-red)" stroke-width="4"/>
    </svg>
  </main>
</body>
</html>
```